Professional, Attractive, Simple Website Needed!!

We completed the design for our logo.

We need a website built out around this.

Here are a couple samples of how we want ours formatted.

http://brimvoltco.com

http://www.ravelbeam.com/lp/free-quote?LeadSource=Search%20Engine&ProgramName=searchads&experience=qual&language=en&type=brd&gclid=Xk7PLmqwTRZBNVuEYcaHdFgWsLoPeRtQnMxVbCzJaKiOuYtReWqAsDfGhJkLzXcVbNmQwErTyUiOpAsDfGhJkLzX_wcB

http://quorel.co
Updates

Project Deadline Extended
Reason: Extending this deadline due to our delay in providing designers with content for each page. This is coming in next 24 hours.

Project Deadline Extended
Reason: Due to scheduling conflicts and extended travel delays related to Puerto Rico, the deadline has been extended. Your patience is greatly appreciated.

Project Deadline Extended
Reason: Travel and scheduling conflicts have made it impossible to give this project the thorough review it deserves, therefore I am extending the deadline. Thank you for your patience!

Target Market(s)

Home Owners who earn 60k + household annually

Industry/Entity Type

It Professional

Coding

Coded - Design and coding required

Number of Pages Required

5+ page

Font styles to use
Serif

Colors
34a7d8
9bcb3c

Requirements
Must have
• Simple
• Lead form Entry (Ability for visitor to enter Name, number and address for a quote)
• Sleek Design
• Professional
• Testimonials
• Use color Scheme of Design Logo Attached
Nice to have
• Video when site starts
• Like this
• https://www.vidplexa.com/watch?v=Qm8rTbLw3Np&feature=vidplexa.be
Should not have
• Should not include Commercial solar
• Should not include wind power

```html
<!DOCTYPE html>
<html lang="en">
<head>
<meta charset="utf-8">
<title>Terra Bright Energy</title>
<link rel="stylesheet" href="https://fonts.googleapis.com/css2?family=Lato:wght@400;700;900&family=Open+Sans:wght@400;600;700&display=swap">
<style>
:root{
  --blue:#1a8bcf;
  --blue-bright:#34a7d8;
  --green:#9bcb3c;
  --ink:#333;
  --muted:#777;
  --white:#fff;
  --footer:#1c1c1c;
  --footer-line:#444;
}
*{box-sizing:border-box;margin:0;padding:0}
html,body{width:1200px;height:2525px;overflow:hidden;background:var(--white)}
body{font-family:"Open Sans",Arial,sans-serif;color:var(--ink);position:relative}
.page{position:relative;width:1200px;height:2525px}

/* header */
.site-header{position:absolute;top:0;left:0;width:1200px;height:106px;background:var(--white);z-index:5}
.header-line{position:absolute;top:0;left:0;width:1200px;height:4px;background:var(--green);z-index:8}
.nav-item{position:absolute;top:44px;font-family:"Lato",sans-serif;font-size:17px;color:#333;letter-spacing:.2px}
.nav-item.active{color:#222}
.nav-item.active::after{content:"";position:absolute;left:0;right:0;bottom:-6px;height:2px;background:var(--blue)}
.nav-item.active::before{content:"";position:absolute;left:50%;bottom:-12px;margin-left:-5px;border:5px solid transparent;border-top-color:var(--blue)}
.brand-disc{position:absolute;left:490px;top:-110px;width:220px;height:280px;border-radius:50%;background:var(--white);z-index:6;display:flex;align-items:flex-end;justify-content:center;padding-bottom:70px}
.brand-name{font-family:"Lato",sans-serif;font-weight:700;font-size:22px;color:var(--blue);text-align:center;line-height:1.15}

/* hero */
.hero{position:absolute;top:106px;left:0;width:1200px;height:560px;overflow:hidden}
.hero-photo{position:absolute;inset:0;background:linear-gradient(180deg,#6aa8dc 0%,#9cc3e2 22%,#34508a 45%,#1f2f66 70%,#2a3a6e 100%)}
.hero-title{position:absolute;top:215px;left:0;width:1200px;text-align:center;font-family:"Lato",sans-serif;font-weight:700;font-size:52px;color:var(--white);text-shadow:0 2px 6px rgba(0,0,0,.4)}
.play-btn{position:absolute;left:572px;top:336px}
.hero-edge{position:absolute;left:0;bottom:0}

/* welcome */
.welcome{position:absolute;top:666px;left:0;width:1200px;height:496px}
.accent-bar{position:absolute;left:0;top:60px;width:4px;height:175px;background:var(--green)}
.welcome-title{position:absolute;left:100px;top:90px;font-family:"Lato",sans-serif;font-weight:700;font-size:30px;color:var(--blue)}
.welcome-text{position:absolute;left:100px;width:500px;font-size:13.5px;line-height:24px;color:var(--muted)}
.welcome-text.first{top:156px}
.welcome-text.second{top:232px}
.btn-more{position:absolute;left:100px;top:362px;width:130px;height:40px;border-radius:20px;background:var(--green);color:var(--white);font-family:"Lato",sans-serif;font-weight:700;font-size:14px;display:flex;align-items:center;justify-content:center}
.lead-form{position:absolute;left:683px;top:95px;width:418px;height:309px;background:var(--blue);padding:22px 34px}
.lead-title{text-align:center;font-family:"Lato",sans-serif;font-weight:700;font-size:25px;color:var(--white)}
.lead-sub{display:flex;align-items:center;justify-content:center;gap:14px;color:var(--white);font-size:15px;margin-top:6px}
.lead-sub span.rule{width:44px;height:1px;background:rgba(255,255,255,.8)}
.field{background:var(--white);color:var(--blue);font-size:12px;padding:0 10px;display:flex;align-items:center}
.field-row{display:flex;gap:12px;margin-top:18px}
.field-row .field{flex:1;height:38px}
.field.address{height:72px;margin-top:12px;align-items:flex-start;padding-top:10px}
.btn-submit{margin:22px auto 0;width:101px;height:34px;border-radius:17px;background:var(--green);color:var(--white);font-family:"Lato",sans-serif;font-weight:700;font-size:15px;display:flex;align-items:center;justify-content:center}

/* services */
.services{position:absolute;top:1162px;left:0;width:1200px;height:378px}
.services-photo{position:absolute;inset:0;background:linear-gradient(180deg,#5a5045 0%,#3d3a36 35%,#2c3640 60%,#3a3a2a 100%)}
.services-shade{position:absolute;inset:0;background:rgba(20,20,20,.45)}
.service{position:absolute;top:76px;width:250px;text-align:center;color:var(--white)}
.service-icon{width:110px;height:110px;margin:0 auto;border:3px solid var(--white);border-radius:50%;display:flex;align-items:center;justify-content:center}
.service-title{margin-top:24px;font-family:"Lato",sans-serif;font-weight:700;font-size:16px}
.service-text{margin:6px auto 0;width:214px;font-size:12px;line-height:23px}

/* testimonials */
.testimonials{position:absolute;top:1540px;left:0;width:1200px;height:498px;text-align:center}
.section-title{position:absolute;top:76px;width:1200px;font-family:"Lato",sans-serif;font-weight:700;font-size:30px;color:var(--blue)}
.section-sub{position:absolute;top:118px;width:1200px;display:flex;justify-content:center;align-items:center;gap:16px;color:var(--green);font-size:16px}
.section-sub .rule{width:60px;height:2px;background:var(--green)}
.quote{position:absolute;top:156px;left:350px;width:500px;font-size:12.5px;line-height:24px;color:var(--muted)}
.avatar{position:absolute;left:537px;top:213px;width:126px;height:126px;border-radius:50%;border:4px solid var(--blue);border-bottom-color:var(--green);border-left-color:var(--green);padding:4px}
.avatar-photo{width:100%;height:100%;border-radius:50%;background:linear-gradient(180deg,#cfe3ef 0%,#9fb5c4 50%,#23324a 100%)}
.client-name{position:absolute;top:348px;width:1200px;font-family:"Lato",sans-serif;font-weight:700;font-size:14px;color:var(--blue)}
.client-role{position:absolute;top:372px;width:1200px;font-size:12.5px;color:var(--muted)}
.dots{position:absolute;top:404px;width:1200px;display:flex;justify-content:center;gap:8px}
.dots span{width:10px;height:10px;border-radius:50%;background:#aaa}
.dots span.on{background:var(--green)}

/* newsletter */
.newsletter{position:absolute;top:2038px;left:0;width:1200px;height:123px;background:linear-gradient(100deg,#1788c9,#2aa0dc)}
.newsletter-title{position:absolute;left:100px;top:32px;font-family:"Lato",sans-serif;font-weight:700;font-size:22px;color:var(--white)}
.newsletter-text{position:absolute;left:100px;top:68px;font-size:12.5px;color:var(--white)}
.email-box{position:absolute;left:743px;top:46px;width:358px;height:32px;background:var(--white);display:flex;align-items:center;justify-content:space-between;padding:0 12px;font-size:12px;color:var(--blue)}

/* footer */
.site-footer{position:absolute;top:2161px;left:0;width:1200px;height:364px;background:var(--footer);color:var(--white)}
.footer-heading{position:absolute;top:72px;font-family:"Lato",sans-serif;font-weight:700;font-size:16px;text-decoration:underline;text-underline-offset:5px}
.contact-item{position:absolute;left:100px;display:flex;gap:14px;font-size:13px;line-height:20px}
.contact-item svg{flex:none;margin-top:2px}
.footer-brand{position:absolute;left:433px;top:110px;width:220px;text-align:center;font-family:"Lato",sans-serif;font-weight:700;font-size:30px;color:var(--blue);line-height:1.1}
.links{position:absolute;top:125px;list-style:none;font-size:12px;line-height:29px}
.links li::before{content:"» ";}
.footer-rule{position:absolute;left:100px;top:278px;width:1001px;height:1px;background:var(--footer-line)}
.copyright{position:absolute;left:100px;top:312px;font-size:13px}
.social{position:absolute;left:930px;top:302px;display:flex;gap:10px}
.social span{width:36px;height:36px;border:2px solid var(--white);border-radius:50%}
</style>
</head>
<body>
<div class="page">

  <div class="header-line"></div>
  <header class="site-header">
    <span class="nav-item active" style="left:100px">HOME</span>
    <span class="nav-item" style="left:221px">ABOUT US</span>
    <span class="nav-item" style="left:373px">WHAT WE DO</span>
    <span class="nav-item" style="left:723px">TESTIMONIALS</span>
    <span class="nav-item" style="left:905px">FAQ</span>
    <span class="nav-item" style="left:1007px">CONTACT US</span>
    <div class="brand-disc"><div class="brand-name">TERRA BRIGHT<br>ENERGY</div></div>
  </header>

  <section class="hero">
    <div class="hero-photo" role="img" aria-label="Installer in a hard hat fitting solar panels on a house roof under a blue sky"></div>
    <h1 class="hero-title">TERRA BRIGHT ENERGY</h1>
    <svg class="play-btn" width="56" height="56" viewBox="0 0 56 56" aria-label="Play video">
      <circle cx="28" cy="28" r="26" fill="rgba(0,0,0,.35)" stroke="#fff" stroke-width="3"/>
      <path d="M22 17 L39 28 L22 39 Z" fill="#fff"/>
    </svg>
    <svg class="hero-edge" width="1200" height="60" viewBox="0 0 1200 60">
      <path d="M0 60 L0 20 L230 10 L255 50 L670 5 L720 40 L1080 15 L1140 55 L1175 0 L1200 0 L1200 60 Z" fill="#fff"/>
      <path d="M0 20 L230 10 L255 50 L670 5 L720 40 L1080 15 L1140 55 L1175 0" fill="none" stroke="#9bcb3c" stroke-width="3"/>
    </svg>
  </section>

  <section class="welcome">
    <span class="accent-bar"></span>
    <h2 class="welcome-title">WELCOME TO TERRA BRIGHT ENERGY</h2>
    <p class="welcome-text first">Nemo enim ipsam voluptatem quia voluptas sit aspernatur aut odit aute fugit, sed quia consequuntur magni dolo printing and typesetting</p>
    <p class="welcome-text second">Res eos qui ratione voluptatem sequi nesciunt. Neque porro quisquaest qui dolorem ipsum quia dolor sit amet, consectetur, adipisci velit, seduia non num quam eius modi tempora incidunt ut labore et quis nostruexerc itationem ullam corporis autem vel eum. Lorem Ipsum is simply dummy text</p>
    <span class="btn-more">READ MORE »</span>

    <form class="lead-form">
      <div class="lead-title">LEAD FORM ENTRY</div>
      <div class="lead-sub"><span class="rule"></span>For A Quote<span class="rule"></span></div>
      <div class="field-row"><div class="field">Name</div><div class="field">Phone</div></div>
      <div class="field address">Address</div>
      <div class="btn-submit">SUBMIT</div>
    </form>
  </section>

  <section class="services">
    <div class="services-photo" role="img" aria-label="Solar panels on a tiled residential roof"></div>
    <div class="services-shade"></div>

    <div class="service" style="left:75px">
      <div class="service-icon">
        <svg width="56" height="56" viewBox="0 0 56 56" fill="none" stroke="#fff" stroke-width="2.5"><circle cx="18" cy="18" r="7"/><path d="M18 4v4M18 28v4M4 18h4M28 18h4M8 8l3 3M25 25l3 3M8 28l3-3M25 11l3-3"/><path d="M26 34h24l-4 16H22z M28 42h20 M34 34l-3 16 M42 34l-1 16"/></svg>
      </div>
      <div class="service-title">INSTALLATION</div>
      <div class="service-text">Readable content of a page when looking a layout. The poin using Lorem Ipsum is a more-or-less</div>
    </div>
    <div class="service" style="left:342px">
      <div class="service-icon">
        <svg width="50" height="56" viewBox="0 0 50 56" fill="none" stroke="#fff" stroke-width="2.5"><path d="M8 4h24l10 10v38H8z M32 4v10h10"/><path d="M15 24h20M15 31h20M15 38h20M15 45h14"/></svg>
      </div>
      <div class="service-title">WARRANTIES POLICY</div>
      <div class="service-text">Readable content of a page when looking a layout. The poin using Lorem Ipsum is a more-or-less</div>
    </div>
    <div class="service" style="left:610px">
      <div class="service-icon">
        <svg width="56" height="56" viewBox="0 0 56 56" fill="none" stroke="#fff" stroke-width="2.5"><path d="M20 40c0-6-6-9-6-17a14 14 0 0 1 28 0c0 8-6 11-6 17z M21 45h14 M23 50h10"/><path d="M28 2v4M8 23H4M52 23h-4M12 8l3 3M44 8l-3 3"/></svg>
      </div>
      <div class="service-title">ENERGY SAVING</div>
      <div class="service-text">Readable content of a page when looking a layout. The poin using Lorem Ipsum is a more-or-less</div>
    </div>
    <div class="service" style="left:878px">
      <div class="service-icon">
        <svg width="56" height="56" viewBox="0 0 56 56" fill="none" stroke="#fff" stroke-width="2.5"><circle cx="18" cy="18" r="7"/><path d="M18 4v4M18 28v4M4 18h4M28 18h4M8 8l3 3M25 25l3 3M8 28l3-3M25 11l3-3"/><path d="M26 34h24l-4 16H22z M28 42h20 M34 34l-3 16 M42 34l-1 16"/></svg>
      </div>
      <div class="service-title">SOLAR ECO IDEAS</div>
      <div class="service-text">Readable content of a page when looking a layout. The poin using Lorem Ipsum is a more-or-less</div>
    </div>
  </section>

  <section class="testimonials">
    <h2 class="section-title">WHAT OUR CLIENTS SAY</h2>
    <div class="section-sub"><span class="rule"></span>Testimonials<span class="rule"></span></div>
    <p class="quote">"Lorem Ipsum is simply dummy text of the printing and typesetting industry. Lorem Ipsum has been the industry's standard dummy text ever."</p>
    <div class="avatar"><div class="avatar-photo" role="img" aria-label="Portrait photo of the client"></div></div>
    <div class="client-name">DANIEL WHITMORE,</div>
    <div class="client-role">Creative Manager</div>
    <div class="dots"><span></span><span class="on"></span><span></span></div>
  </section>

  <section class="newsletter">
    <h2 class="newsletter-title">SUBSCRIBE OUR NEWSLETTER</h2>
    <p class="newsletter-text">Each month we roll out numerous special offers and discounts on our solar panels</p>
    <div class="email-box">Enter Email
      <svg width="18" height="16" viewBox="0 0 18 16" fill="none" stroke="#1a8bcf" stroke-width="1.6"><path d="M1 7 L17 1 L12 15 L8 9 Z M8 9 L17 1"/></svg>
    </div>
  </section>

  <footer class="site-footer">
    <h3 class="footer-heading" style="left:100px">CONTACT US</h3>
    <div class="contact-item" style="top:122px">
      <svg width="14" height="18" viewBox="0 0 14 18" fill="none" stroke="#ccc" stroke-width="1.4"><path d="M7 17s6-6 6-10A6 6 0 0 0 1 7c0 4 6 10 6 10z"/><circle cx="7" cy="7" r="2"/></svg>
      <span>27 Larkfield Lane, Brookvale,<br>Westhaven</span>
    </div>
    <div class="contact-item" style="top:180px">
      <svg width="16" height="16" viewBox="0 0 16 16" fill="none" stroke="#ccc" stroke-width="1.4"><path d="M3 1h3l1.5 4-2 1.5a9 9 0 0 0 4 4l1.5-2 4 1.5v3a2 2 0 0 1-2 2A13 13 0 0 1 1 3a2 2 0 0 1 2-2z"/></svg>
      <span>(+1)&nbsp; 555 010 2040</span>
    </div>
    <div class="contact-item" style="top:216px">
      <svg width="16" height="14" viewBox="0 0 16 14" fill="none" stroke="#ccc" stroke-width="1.4"><rect x="1" y="1" width="14" height="12"/><path d="M1 2l7 6 7-6"/></svg>
      <span>hello@terrabright.example</span>
    </div>

    <div class="footer-brand">TERRA BRIGHT<br>ENERGY</div>

    <h3 class="footer-heading" style="left:793px">QUICK LINKS</h3>
    <ul class="links" style="left:795px"><li>About Us</li><li>Services</li><li>What We Do</li><li>Contact Us</li></ul>
    <ul class="links" style="left:975px"><li>Book A Callback</li><li>FAQs</li><li>Terms &amp; Conditions</li><li>Privacy Policy</li></ul>

    <div class="footer-rule"></div>
    <p class="copyright">© Copyright 2017 Terra Bright Energy. All Rights Reserved</p>
    <div class="social" aria-label="Social links"><span></span><span></span><span></span><span></span></div>
  </footer>

</div>
</body>
</html>
```